5 x Packaging Design - Most of the design style is already done!

The logo is "Ember Over Tide" which will remain the same. The font is Athens.

We just require realistic packaging design with the fronts of the packaging. Together/ seperate/ in different mockup backdrops etc.

CLAY MASKS: BLACK JAR WHITE LID:
- the cursive coloured font is "Majesty"
- If you think you can design something even more attractive go for it! but we like the design a lot.
- Most important for us is to make it look realistic on the packaging so that we can use it on the website :)

BEARD OIL: BLACK JAR WITH SILVER AND WHITE PUMP LID:
- You are free to design similar/same or completely different

competitors:
Morvelle
reedandmoss

Industry/Entity Type

Cosmetics

```html
<!DOCTYPE html>
<html lang="en">
<head>
<meta charset="utf-8">
<title>Ember Over Tide Beard Oil Label</title>
<link rel="stylesheet" href="https://fonts.googleapis.com/css2?family=Josefin+Sans:wght@300&family=Oswald:wght@300&family=Pathway+Gothic+One&family=Yellowtail&display=swap">
<style>
  :root {
    --label-black: #0b0a0a;
    --ink-white: #f4f2ee;
    --ink-grey: #6f6c69;
    --rule-white: #ecebe7;
  }
  * { margin: 0; padding: 0; box-sizing: border-box; }
  html, body {
    width: 1200px;
    height: 619px;
    overflow: hidden;
    background: var(--label-black);
  }
  .label {
    position: relative;
    width: 1200px;
    height: 619px;
    display: flex;
    flex-direction: column;
    align-items: center;
    color: var(--ink-white);
  }
  .brand-name {
    margin-top: 92px;
    font-family: "Josefin Sans", sans-serif;
    font-weight: 300;
    font-size: 30px;
    letter-spacing: 14px;
    text-transform: uppercase;
    color: var(--ink-white);
  }
  .tagline-row {
    margin-top: 46px;
    display: flex;
    align-items: center;
    gap: 18px;
  }
  .tagline-rule {
    width: 64px;
    height: 2px;
    background: var(--rule-white);
  }
  .tagline {
    font-family: "Pathway Gothic One", sans-serif;
    font-size: 36px;
    letter-spacing: 1px;
    text-transform: uppercase;
  }
  .full-rule {
    width: 500px;
    height: 3px;
    background: var(--rule-white);
  }
  .full-rule.upper { margin-top: 8px; transform: rotate(-2deg); }
  .full-rule.lower { margin-top: 8px; transform: rotate(-2deg); }
  .product-name {
    margin-top: 14px;
    font-family: "Yellowtail", cursive;
    font-size: 112px;
    line-height: 1.1;
    color: var(--ink-white);
    transform: rotate(-2deg);
  }
  .scent {
    margin-top: 30px;
    font-family: "Oswald", sans-serif;
    font-weight: 300;
    font-size: 44px;
    letter-spacing: 2px;
    text-transform: uppercase;
    color: var(--ink-grey);
  }
  .volume {
    margin-top: 40px;
    font-family: "Pathway Gothic One", sans-serif;
    font-size: 24px;
    letter-spacing: 1px;
    color: var(--ink-white);
  }
</style>
</head>
<body>
  <main class="label">
    <p class="brand-name">Ember Over Tide</p>
    <div class="tagline-row">
      <span class="tagline-rule"></span>
      <span class="tagline">Premium Organic</span>
      <span class="tagline-rule"></span>
    </div>
    <div class="full-rule upper"></div>
    <h1 class="product-name">Beard Oil</h1>
    <div class="full-rule lower"></div>
    <p class="scent">Patchouli</p>
    <p class="volume">30ML</p>
  </main>
</body>
</html>
```